Quorva - corporate Business Card

We need a good look and innovative business card for a new start up company based in Los Angeles called "Quorva". We are in a payment business, including payment card, app, and ewallet. We are expert in online payment and Card not present (CNP) transaction.
We need an innovative, modern business card.

Our logo font is Aero Matics

Target Market(s)

Startup - Bank - Online Payment - Card Manufacturing

Industry/Entity Type

Startup

Contact Information for Business Card

phone: 555 014 7396 - Address: 4172 Marlowe blvd, Ardenvale, NV 89411

Requirements
Must have
• Message: innovative, professional, expert, high tech, trust, online payment expert, security
Nice to have
• no comment
Should not have
• no Comment

```html
<!DOCTYPE html>
<html lang="en">
<head>
<meta charset="utf-8">
<title>Quorva — Business Card</title>
<link rel="stylesheet" href="https://fonts.googleapis.com/css2?family=Lato:wght@400;700;900&display=swap">
<style>
  :root {
    --brand-red: #b7202f;
    --card-white: #ffffff;
    --ink-grey: #555a60;
    --backdrop: #1c1d20;
  }
  * { box-sizing: border-box; margin: 0; padding: 0; }
  html, body {
    width: 1200px; height: 900px; overflow: hidden;
    background: var(--backdrop);
    font-family: "Lato", sans-serif;
  }
  .stage {
    width: 1200px; height: 900px;
    display: flex; flex-direction: column; align-items: center; justify-content: center;
    gap: 36px;
  }
  .card {
    width: 700px; height: 400px;
    border-radius: 30px;
    position: relative;
    overflow: hidden;
    box-shadow: 0 12px 30px rgba(0,0,0,.45);
  }
  /* Front */
  .card--front {
    background: var(--brand-red);
    display: flex; align-items: center;
    padding-left: 70px; gap: 28px;
  }
  .front-dot {
    width: 150px; height: 150px; border-radius: 50%;
    background: var(--card-white);
    flex: none;
  }
  .front-name {
    color: var(--card-white);
    font-weight: 700;
    font-size: 120px;
    letter-spacing: 1px;
    line-height: 1;
    padding-bottom: 12px;
  }
  /* Back */
  .card--back {
    background: var(--card-white);
  }
  .back-mark {
    position: absolute; left: 70px; top: 60px;
    width: 280px; height: 280px; border-radius: 50%;
    background: var(--brand-red);
    display: flex; align-items: center; justify-content: center;
  }
  .back-mark__name {
    color: var(--card-white);
    font-weight: 700;
    font-size: 54px;
  }
  .divider {
    position: absolute; left: 400px; top: 58px;
    width: 2px; height: 268px;
    background: var(--brand-red);
  }
  .contact {
    position: absolute; left: 420px; top: 50px;
    color: var(--ink-grey);
  }
  .contact__name {
    color: var(--brand-red);
    font-weight: 900;
    font-size: 28px;
    line-height: 1.1;
  }
  .contact__title {
    font-size: 19px;
    margin-bottom: 10px;
  }
  .contact__list { list-style: none; }
  .contact__item {
    display: flex; align-items: center; gap: 10px;
    font-size: 19px; line-height: 1.5;
  }
  .contact__item--phone { letter-spacing: 3px; }
  .contact__icon { width: 16px; height: 16px; flex: none; fill: var(--brand-red); }
  .contact__address {
    margin-top: 14px;
    font-size: 18px; line-height: 1.3;
  }
</style>
</head>
<body>
<main class="stage">
  <section class="card card--front" aria-label="Card front">
    <span class="front-dot" aria-hidden="true"></span>
    <span class="front-name">quorva</span>
  </section>

  <section class="card card--back" aria-label="Card back">
    <div class="back-mark"><span class="back-mark__name">Quorva</span></div>
    <span class="divider" aria-hidden="true"></span>
    <div class="contact">
      <p class="contact__name">Lena Harrow</p>
      <p class="contact__title">President</p>
      <ul class="contact__list">
        <li class="contact__item contact__item--phone">
          <svg class="contact__icon" viewBox="0 0 16 16" aria-hidden="true"><path d="M3.5 1.5l2.5 0 1 3.5-1.6 1.2c.8 1.8 2.2 3.2 4 4L10.6 8.6 14 9.6v2.6c0 .9-.8 1.6-1.7 1.5C6.8 13.2 2.6 9 2 3.4 1.9 2.4 2.6 1.5 3.5 1.5z"/></svg>
          555. 014. 7396
        </li>
        <li class="contact__item contact__item--phone">
          <svg class="contact__icon" viewBox="0 0 16 16" aria-hidden="true"><path d="M4.5 1h7c.6 0 1 .4 1 1v12c0 .6-.4 1-1 1h-7c-.6 0-1-.4-1-1V2c0-.6.4-1 1-1zm.8 1.8v9.4h5.4V2.8zM8 12.8a.7.7 0 100 1.4.7.7 0 000-1.4z"/></svg>
          555. 207. 4813
        </li>
        <li class="contact__item">
          <svg class="contact__icon" viewBox="0 0 16 16" aria-hidden="true"><path d="M1 3.5h14v9H1zm1.4 1L8 8.8l5.6-4.3z"/></svg>
          lena@quorva.com
        </li>
        <li class="contact__item">
          <svg class="contact__icon" viewBox="0 0 16 16" aria-hidden="true"><path d="M8 1a7 7 0 100 14A7 7 0 008 1zm-1 1.9v2.6H4.2A5.6 5.6 0 017 2.9zm2 0a5.6 5.6 0 012.8 2.6H9zM2.5 7h4.5v2H2.5a5.6 5.6 0 010-2zm6.5 0h4.5a5.6 5.6 0 010 2H9zm-4.8 3.5H7v2.6a5.6 5.6 0 01-2.8-2.6zm4.8 0h2.8A5.6 5.6 0 019 13.1z"/></svg>
          www.quorva.com
        </li>
      </ul>
      <p class="contact__address">4172 Marlowe blvd<br>Ardenvale, NV 89411</p>
    </div>
  </section>
</main>
</body>
</html>
```